Wedding Videography Wordpress Website Theme

We need a modern and high-end website look for our wedding video and film business. We film weddings all over the United Kingdom and at European destinations so need something to reflect our work. The website should be visually stunning with images and videos being the focal point as this is what our services are.

The current website is www.brunolessway.com so you will be able to see our brand.

My Instagram is www.instagram.com/brunolesswayfilms so a new design should link in with this idea.

We need the following pages designed by the winning designer

1 - Homepage
2 - Films Index Page
3 - Testimonials
4 - Prices
5 - Reviews
6 - Meet Bruno (About)
7 - Contact
8 - Blog Index
9 - Blog Page

All pages must be consistent so have a similar style.

Pages on menu:
Meet Bruno
Videos
Packages
Testimionials
Journal (Blog)
Contact

We require a responsive look too. Over 90% of our visitors access the website via their mobile devices.

```html
<!DOCTYPE html>
<html lang="en">
<head>
<meta charset="utf-8">
<title>Bruno Lessway Wedding Films</title>
<link rel="stylesheet" href="https://fonts.googleapis.com/css2?family=Cormorant+Garamond:wght@400;500;600&family=Jost:wght@300;400;500&family=Great+Vibes&display=swap">
<style>
:root{
  --gold:#b8975a;
  --gold-light:#d9c08e;
  --sand:#e9dcbc;
  --ink:#1b1b1b;
  --ink-soft:#2a2a2a;
  --text:#4a4a4a;
  --muted:#8a8a8a;
  --white:#ffffff;
  --serif:"Cormorant Garamond", Georgia, serif;
  --sans:"Jost", Arial, sans-serif;
  --script:"Great Vibes", cursive;
}
*{margin:0;padding:0;box-sizing:border-box}
html,body{width:1200px;height:5096px;overflow:hidden}
body{font-family:var(--sans);color:var(--text);background:var(--white);position:relative}
section,header,footer{position:relative;width:1200px;overflow:hidden}
.media{position:absolute;display:block}
.btn{display:inline-block;font-family:var(--sans);font-weight:500;font-size:13px;letter-spacing:1.5px;text-transform:uppercase;color:var(--ink);background:var(--sand);padding:13px 26px;text-decoration:none}
.play{position:absolute;width:52px;height:52px;border-radius:50%;border:1.5px solid rgba(255,255,255,.85);display:flex;align-items:center;justify-content:center;background:rgba(255,255,255,.15);z-index:2}
.play svg{margin-left:4px}

/* Hero */
.hero{height:616px;background:#15170f}
.hero .media{inset:0;background:
  radial-gradient(ellipse 180px 300px at 800px 330px,rgba(236,230,214,.55),rgba(236,230,214,0) 70%),
  radial-gradient(ellipse 120px 260px at 880px 250px,rgba(20,20,22,.85),rgba(20,20,22,0) 75%),
  radial-gradient(ellipse 500px 300px at 1000px 120px,#6f7a4a,rgba(111,122,74,0) 70%),
  radial-gradient(ellipse 420px 340px at 180px 220px,#3c4a2a,rgba(60,74,42,0) 70%),
  linear-gradient(180deg,#1f2618 0%,#2d3822 45%,#171b12 100%)}
.hero::after{content:"";position:absolute;inset:0;background:linear-gradient(180deg,rgba(0,0,0,.45) 0%,rgba(0,0,0,0) 25%,rgba(0,0,0,0) 70%,rgba(0,0,0,.5) 100%)}
.nav{position:absolute;top:22px;left:0;right:0;height:60px;z-index:3}
.brand{position:absolute;left:120px;top:0;display:flex;align-items:center;gap:12px;text-decoration:none}
.brand-mark{width:14px;height:14px;border-radius:50%;background:var(--white)}
.brand-name{font-family:var(--sans);font-weight:400;font-size:18px;letter-spacing:5px;color:var(--white);text-transform:uppercase}
.menu{position:absolute;left:392px;top:44px;transform:translateY(-50%);display:flex;gap:42px;list-style:none}
.menu a{color:var(--white);font-size:13px;letter-spacing:1.6px;text-transform:uppercase;text-decoration:none}
.nav .btn{position:absolute;right:114px;top:30px}
.hero .play{left:568px;top:292px}
.play-label{position:absolute;left:560px;top:364px;z-index:2;font-family:var(--script);font-size:20px;color:var(--white)}
.couple-tag{position:absolute;left:116px;top:532px;z-index:2;display:flex;align-items:center;gap:14px;color:var(--white);font-size:14px;letter-spacing:2px}
.couple-tag .avatar{width:46px;height:46px;border-radius:50%;background:radial-gradient(circle at 40% 40%,#d8c7a6,#5a4e3d 75%)}
.next{position:absolute;right:120px;top:504px;z-index:2;display:flex;align-items:center}
.next-text{background:rgba(20,20,20,.75);width:120px;height:88px;padding:20px 18px;color:var(--white)}
.next-text strong{display:block;font-family:var(--serif);font-weight:500;font-size:26px;letter-spacing:2px}
.next-text span{font-size:11px;letter-spacing:.5px}
.next .media{position:relative;width:124px;height:88px;background:radial-gradient(ellipse at 45% 50%,#e7e1d2 0%,#8d8b70 35%,#3a3c2c 85%)}

/* Showcase */
.showcase{height:1404px;padding-top:56px;text-align:center}
.section-title{font-family:var(--serif);font-weight:500;font-size:34px;letter-spacing:3px;text-transform:uppercase;color:var(--gold)}
.film-grid{position:absolute;left:112px;top:132px;display:grid;grid-template-columns:468px 464px;column-gap:40px;row-gap:36px}
.film{position:relative;height:340px;overflow:hidden}
.film .media{inset:0}
.film .play{left:50%;top:50%;transform:translate(-50%,-50%)}
.film-name{position:absolute;left:30px;bottom:22px;z-index:2;font-family:var(--script);font-size:34px;color:var(--white);text-shadow:0 1px 6px rgba(0,0,0,.4)}
.film:nth-child(even) .film-name{left:auto;right:30px}
.showcase .btn{position:absolute;left:492px;top:1316px;width:216px;padding:13px 0;text-align:center;font-size:12px}

/* 360 band */
.panorama{height:492px;background:#2c3326}
.panorama .media{inset:0;background:
  radial-gradient(ellipse 90px 70px at 140px 260px,#26301c,rgba(38,48,28,0) 80%),
  radial-gradient(ellipse 70px 200px at 600px 420px,rgba(190,186,170,.55),rgba(190,186,170,0) 80%),
  linear-gradient(180deg,#5d6455 0%,#4a553a 18%,#2f3a22 28%,#56643c 45%,#3b4a29 70%,#202a17 100%)}
.panorama::after{content:"";position:absolute;inset:0;background:rgba(0,0,0,.18)}
.panorama-copy{position:absolute;left:0;right:0;top:184px;text-align:center;color:var(--white);z-index:2}
.panorama-copy h2{font-family:var(--serif);font-weight:500;font-size:34px;letter-spacing:3px;text-transform:uppercase}
.panorama-copy p{margin-top:10px;font-size:16px;font-weight:300;letter-spacing:.4px}

/* Moments */
.moments{height:612px;margin-top:68px}
.moments .media{left:112px;top:0;width:480px;height:492px;background:
  radial-gradient(ellipse 90px 220px at 100px 300px,#1c1a1a,rgba(28,26,26,0) 80%),
  radial-gradient(ellipse 100px 200px at 300px 320px,rgba(240,236,228,.85),rgba(240,236,228,0) 80%),
  radial-gradient(ellipse 80px 160px at 250px 120px,#a8322b,rgba(168,50,43,0) 80%),
  linear-gradient(160deg,#e7e3dc 0%,#9c948a 35%,#4a433d 70%,#2a2522 100%)}
.moments .play{left:326px;top:220px}
.moments-copy{position:absolute;left:632px;top:96px;width:440px}
.moments-copy h2{font-family:var(--serif);font-weight:600;font-size:28px;line-height:1.3;letter-spacing:2px;text-transform:uppercase;color:var(--gold)}
.moments-copy p{margin-top:18px;font-size:13px;line-height:1.8;color:var(--text)}
.quote{margin-top:22px;display:flex;align-items:center;gap:16px}
.quote .avatar{width:64px;height:64px;border-radius:50%;background:radial-gradient(circle at 45% 40%,#e2d3bb,#6e6152 75%)}
.quote strong{display:block;font-weight:500;font-size:15px;color:var(--ink)}
.quote span{font-size:12px;color:var(--muted)}

/* Story band */
.story{height:560px;background:var(--ink)}
.story .media{inset:0;background:
  radial-gradient(ellipse 160px 200px at 1010px 330px,rgba(238,236,230,.75),rgba(238,236,230,0) 80%),
  radial-gradient(ellipse 170px 220px at 1090px 300px,#111,rgba(17,17,17,0) 80%),
  radial-gradient(ellipse 160px 160px at 620px 480px,rgba(225,222,216,.6),rgba(225,222,216,0) 80%),
  radial-gradient(ellipse 260px 200px at 860px 110px,#3f4a30,rgba(63,74,48,0) 80%),
  linear-gradient(90deg,#0f0f0f 0%,#181917 40%,#2c2c27 70%,#141414 100%)}
.story-frame{position:absolute;left:96px;top:124px;width:410px;height:300px;border:1px solid var(--gold);border-right:none;z-index:2}
.story-copy{position:absolute;left:132px;top:164px;color:var(--white);z-index:2}
.story-copy .kicker{font-family:var(--serif);font-size:30px;font-weight:400}
.story-copy h2{margin-top:14px;font-family:var(--serif);font-weight:500;font-size:46px;line-height:1.12;color:var(--gold-light)}
.story-copy .btn{margin-top:26px;font-size:12px;padding:11px 22px}

/* Sound */
.sound{height:552px;text-align:center;padding-top:84px}
.sound p{width:800px;margin:22px auto 0;font-size:13px;line-height:1.85;color:var(--text)}
.sound .media{left:0;top:272px;width:1200px;height:280px;background:
  radial-gradient(ellipse 220px 70px at 560px 170px,#b9b9b9,rgba(185,185,185,0) 80%),
  radial-gradient(ellipse 300px 80px at 200px 110px,#2a2a2a,rgba(42,42,42,0) 80%),
  radial-gradient(ellipse 300px 80px at 1000px 110px,#333,rgba(51,51,51,0) 80%),
  linear-gradient(180deg,#f4f4f4 0%,#cfcfcf 22%,#6e6e6e 38%,#545454 60%,#2e2e2e 100%)}

/* Instagram */
.instagram{height:560px;background:var(--sand);text-align:center;padding-top:48px}
.instagram .section-title{color:var(--ink-soft);letter-spacing:6px}
.insta-row{position:absolute;left:112px;top:132px;display:flex;gap:12px}
.insta-row .media{position:relative;width:152px;height:160px}
.instagram .btn{position:absolute;left:472px;top:352px;width:256px;padding:16px 0;background:var(--white);text-transform:none;letter-spacing:.3px;font-weight:400;font-size:14px}

/* Footer */
.site-footer{height:296px;background:var(--white)}
.footer-brand{position:absolute;left:120px;top:64px;display:flex;align-items:center;gap:10px}
.footer-brand .brand-mark{background:var(--gold);width:12px;height:12px}
.footer-brand .brand-name{color:var(--gold);font-size:16px;letter-spacing:4px}
.socials{position:absolute;left:150px;top:150px;display:flex;gap:12px}
.socials span{width:26px;height:26px;border-radius:50%;border:1.5px solid var(--gold)}
.footer-col{position:absolute;top:72px}
.footer-col h3{font-family:var(--sans);font-weight:500;font-size:16px;color:var(--ink);margin-bottom:16px}
.footer-col li{list-style:none;font-size:13px;color:var(--text);margin-bottom:12px;display:flex;align-items:center;gap:12px}
.footer-col svg{flex:none}
.col-contact{left:412px}
.col-links{left:700px}
.col-more{left:912px;top:112px}
.copyright{position:absolute;left:0;right:0;top:262px;text-align:center;font-size:11px;color:var(--muted)}
</style>
</head>
<body>

<header class="hero">
  <div class="media" role="img" aria-label="Bride and groom embracing in a wooded garden, film still"></div>
  <nav class="nav">
    <a class="brand" href="#"><span class="brand-mark"></span><span class="brand-name">Bruno Lessway</span></a>
    <ul class="menu">
      <li><a href="#">Meet Bruno</a></li>
      <li><a href="#">Videos</a></li>
      <li><a href="#">Packages</a></li>
      <li><a href="#">Testimonials</a></li>
      <li><a href="#">Journal</a></li>
    </ul>
    <a class="btn" href="#">Enquire</a>
  </nav>
  <span class="play"><svg width="16" height="18" viewBox="0 0 16 18"><path d="M0 0L16 9L0 18Z" fill="#fff"/></svg></span>
  <span class="play-label">Play Video</span>
  <div class="couple-tag"><span class="avatar" role="img" aria-label="Couple portrait thumbnail"></span>ELLIS + ROWAN</div>
  <div class="next">
    <div class="next-text"><strong>NEXT</strong><span>Isla &amp; Callum</span></div>
    <div class="media" role="img" aria-label="Next wedding film thumbnail"></div>
  </div>
</header>

<section class="showcase">
  <h2 class="section-title">Video Showcase</h2>
  <div class="film-grid">
    <article class="film"><div class="media" role="img" aria-label="Couple walking through confetti" style="background:radial-gradient(ellipse 90px 160px at 300px 200px,rgba(238,232,220,.8),rgba(238,232,220,0) 80%),radial-gradient(ellipse 90px 180px at 140px 210px,#161616,rgba(22,22,22,0) 80%),radial-gradient(ellipse 120px 90px at 390px 190px,#8a3a44,rgba(138,58,68,0) 80%),linear-gradient(135deg,#7a6550,#3a2d24 60%,#221a15)"></div><span class="play"><svg width="16" height="18" viewBox="0 0 16 18"><path d="M0 0L16 9L0 18Z" fill="#fff"/></svg></span><span class="film-name">Hattie and Owen</span></article>
    <article class="film"><div class="media" role="img" aria-label="Couple laughing outdoors" style="background:radial-gradient(ellipse 120px 140px at 320px 150px,#d9c2a4,rgba(217,194,164,0) 80%),radial-gradient(ellipse 110px 160px at 160px 230px,#1e1e1e,rgba(30,30,30,0) 80%),radial-gradient(ellipse 120px 120px at 330px 280px,rgba(240,236,230,.8),rgba(240,236,230,0) 80%),linear-gradient(135deg,#8d9a6a,#4e5c38 60%,#2f3a22)"></div><span class="play"><svg width="16" height="18" viewBox="0 0 16 18"><path d="M0 0L16 9L0 18Z" fill="#fff"/></svg></span><span class="film-name">Clara and Dominic</span></article>
    <article class="film"><div class="media" role="img" aria-label="Couple walking across a field" style="background:radial-gradient(ellipse 50px 110px at 180px 200px,#1b1b1b,rgba(27,27,27,0) 80%),radial-gradient(ellipse 70px 110px at 280px 230px,rgba(245,242,236,.9),rgba(245,242,236,0) 80%),linear-gradient(180deg,#6e6a4e 0%,#c4a57e 20%,#b08e66 60%,#7c6146 100%)"></div><span class="play"><svg width="16" height="18" viewBox="0 0 16 18"><path d="M0 0L16 9L0 18Z" fill="#fff"/></svg></span><span class="film-name">Imogen and Felix</span></article>
    <article class="film"><div class="media" role="img" aria-label="Couple standing on a lawn" style="background:radial-gradient(ellipse 60px 150px at 270px 190px,#1c2130,rgba(28,33,48,0) 80%),radial-gradient(ellipse 55px 140px at 230px 200px,rgba(240,238,232,.85),rgba(240,238,232,0) 80%),linear-gradient(180deg,#596b44 0%,#718452 45%,#5d7143 70%,#34421f 100%)"></div><span class="play"><svg width="16" height="18" viewBox="0 0 16 18"><path d="M0 0L16 9L0 18Z" fill="#fff"/></svg></span><span class="film-name">Tessa and Maya</span></article>
    <article class="film"><div class="media" role="img" aria-label="Wedding rings close up" style="background:radial-gradient(ellipse 70px 40px at 230px 190px,#c9b48a,rgba(201,180,138,0) 80%),radial-gradient(ellipse 260px 140px at 230px 220px,#6b4a2a,rgba(107,74,42,0) 80%),linear-gradient(180deg,#3a2c20,#1a120c)"></div><span class="play"><svg width="16" height="18" viewBox="0 0 16 18"><path d="M0 0L16 9L0 18Z" fill="#fff"/></svg></span><span class="film-name">Rosa and Idris</span></article>
    <article class="film"><div class="media" role="img" aria-label="Couple on a stone bridge in black and white" style="background:radial-gradient(ellipse 250px 70px at 230px 150px,#b4b4b4,rgba(180,180,180,0) 80%),radial-gradient(ellipse 240px 90px at 230px 270px,#1e1e1e,rgba(30,30,30,0) 80%),linear-gradient(180deg,#5c5c5c 0%,#8e8e8e 40%,#4a4a4a 75%,#252525 100%)"></div><span class="play"><svg width="16" height="18" viewBox="0 0 16 18"><path d="M0 0L16 9L0 18Z" fill="#fff"/></svg></span><span class="film-name">Freya &amp; Lewis</span></article>
  </div>
  <a class="btn" href="#">Load More Video</a>
</section>

<section class="panorama">
  <div class="media" role="img" aria-label="Aerial view of a country venue and its grounds"></div>
  <div class="panorama-copy">
    <h2>Capturing the full 360</h2>
    <p>Enjoy the full cinematic feel with stunning aerial shots of your venue.</p>
  </div>
</section>

<section class="moments">
  <div class="media" role="img" aria-label="Couple walking out of the ceremony"></div>
  <span class="play"><svg width="16" height="18" viewBox="0 0 16 18"><path d="M0 0L16 9L0 18Z" fill="#fff"/></svg></span>
  <div class="moments-copy">
    <h2>Once in a lifetime moments<br>you'll never forget</h2>
    <p>You pick up all kinds of wonderful surprises when the camera's rolling. This extra special one you'll want to treasure forever. Look what happened here when Theo revealed his and Ada's big secret.</p>
    <div class="quote">
      <span class="avatar" role="img" aria-label="Couple portrait"></span>
      <div><strong>Theo and Ada</strong><span>Have a special announcement to make</span></div>
    </div>
  </div>
</section>

<section class="story">
  <div class="media" role="img" aria-label="Bride and groom in an evening portrait"></div>
  <div class="story-frame"></div>
  <div class="story-copy">
    <p class="kicker">Your wedding has a story</p>
    <h2>Relive your moments<br>for a lifetime.</h2>
    <a class="btn" href="#">Enquire</a>
  </div>
</section>

<section class="sound">
  <h2 class="section-title">Did you hear that?</h2>
  <p>There's a whole gamut of emotions wrapped up in your wedding day bubble. So don't risk forgetting the sounds as well as the sights. The giggles, the vows, the jokes, the speeches, and the music add atmosphere to your wedding video and bring your day back to life each and every time you watch it. Memories of what was said, a certain person's signature laugh, and the things that were shared will fade over time. So imagine how special it will be twenty years on to enjoy your own film with your next generation and be reminded of those extra special sounds again.</p>
  <div class="media" role="img" aria-label="Black and white aerial view of a stately home"></div>
</section>

<section class="instagram">
  <h2 class="section-title">Follow me on Instagram</h2>
  <div class="insta-row">
    <div class="media" role="img" aria-label="Instagram post: couple portrait" style="background:radial-gradient(ellipse 40px 70px at 60px 95px,#1e1e1e,rgba(30,30,30,0) 80%),radial-gradient(ellipse 40px 70px at 100px 100px,rgba(240,236,230,.85),rgba(240,236,230,0) 80%),linear-gradient(180deg,#b9ad98,#6d6150)"></div>
    <div class="media" role="img" aria-label="Instagram post: bride and groom" style="background:radial-gradient(ellipse 40px 80px at 50px 90px,#22252e,rgba(34,37,46,0) 80%),radial-gradient(ellipse 45px 80px at 105px 100px,rgba(245,242,238,.9),rgba(245,242,238,0) 80%),linear-gradient(180deg,#d6d0c6,#8a8176)"></div>
    <div class="media" role="img" aria-label="Instagram post: wedding car" style="background:radial-gradient(ellipse 60px 30px at 76px 110px,#f0ece4,rgba(240,236,228,0) 80%),linear-gradient(180deg,#b6c0c6 0%,#9ea67f 40%,#6f6a4e 100%)"></div>
    <div class="media" role="img" aria-label="Instagram post: groom in suit" style="background:radial-gradient(ellipse 50px 90px at 80px 110px,#111,rgba(17,17,17,0) 80%),radial-gradient(ellipse 30px 60px at 40px 100px,#b23a2e,rgba(178,58,46,0) 80%),linear-gradient(180deg,#8f8a82,#3a3834)"></div>
    <div class="media" role="img" aria-label="Instagram post: ceremony" style="background:radial-gradient(ellipse 40px 80px at 55px 100px,#1e1e1e,rgba(30,30,30,0) 80%),radial-gradient(ellipse 40px 80px at 105px 100px,rgba(238,232,222,.85),rgba(238,232,222,0) 80%),linear-gradient(180deg,#c4b59c,#6d5f4d)"></div>
    <div class="media" role="img" aria-label="Instagram post: outdoor celebration" style="background:radial-gradient(ellipse 50px 70px at 80px 110px,rgba(240,238,232,.8),rgba(240,238,232,0) 80%),linear-gradient(180deg,#b4c4d0 0%,#98a98a 45%,#5e6f45 100%)"></div>
  </div>
  <a class="btn" href="#">Follow me @brunolesswayfilms</a>
</section>

<footer class="site-footer">
  <div class="footer-brand"><span class="brand-mark"></span><span class="brand-name">Bruno Lessway</span></div>
  <div class="socials"><span></span><span></span><span></span></div>
  <div class="footer-col col-contact">
    <h3>Contact</h3>
    <ul>
      <li><svg width="16" height="16" viewBox="0 0 24 24"><path d="M6.6 10.8a15.1 15.1 0 006.6 6.6l2.2-2.2c.3-.3.7-.4 1-.2 1.1.4 2.3.6 3.6.6.6 0 1 .4 1 1V20c0 .6-.4 1-1 1A17 17 0 013 4c0-.6.4-1 1-1h3.5c.6 0 1 .4 1 1 0 1.3.2 2.5.6 3.6.1.3 0 .7-.2 1z" fill="none" stroke="#b8975a" stroke-width="1.6"/></svg>07700 900 418</li>
      <li><svg width="16" height="16" viewBox="0 0 24 24"><rect x="3" y="5" width="18" height="14" fill="none" stroke="#b8975a" stroke-width="1.6"/><path d="M3 6l9 7 9-7" fill="none" stroke="#b8975a" stroke-width="1.6"/></svg>hello@brunolessway.com</li>
    </ul>
  </div>
  <div class="footer-col col-links">
    <h3>Links</h3>
    <ul>
      <li>FAQ's</li>
      <li>Wedding Photography</li>
      <li>Commercial</li>
    </ul>
  </div>
  <div class="footer-col col-more">
    <ul>
      <li>North East Wedding Venues</li>
      <li>Free Speeches Guide</li>
      <li>Blog</li>
    </ul>
  </div>
  <p class="copyright">© Copyright 2022 Bruno Lessway Films. All Rights Reserved.</p>
</footer>

</body>
</html>
```